Harborline Renewal Business Card Design

Professional and clean design. The design colors should flow with the logo. Two-sided card with the website on the back which is:

www.HarborlineRenewal.example.

"Specializing in Water Damage Restoration"

On the front I need the name, email, phone, and logo.

Name: Darnell Quisby
Email: Darnell@HarborlineRenewal.example
Phone: 555-318-2046 for now

I only have the Preview and Thumbnail right now but should have the source files uploaded within a day or two.

Target Market(s)

Flood victims, home owners with water damage from busted pipes etc...

Industry/Entity Type

Business

Contact Information for Business Card

Name: Darnell Quisby

Font styles to use
Serif
Sans Serif

Requirements
Must have
• Business Card Details Info

```html
<!DOCTYPE html>
<html lang="en">
<head>
<meta charset="utf-8">
<title>Harborline Renewal Business Card</title>
<link rel="stylesheet" href="https://fonts.googleapis.com/css2?family=Cinzel:wght@400;600&family=Open+Sans:wght@400&display=swap">
<style>
  :root {
    --page-bg: #e9ecef;
    --card-bg: #ffffff;
    --brand-blue: #2a8fd0;
    --wave-light: #5bbfee;
    --wave-dark: #2a86c8;
    --faint-circle: #d9eef9;
    --text-dark: #1f3442;
    --text-body: #333a40;
    --text-muted: #5d646a;
    --divider: #d2d6d9;
  }
  * { box-sizing: border-box; margin: 0; padding: 0; }
  html, body { width: 1200px; height: 1120px; overflow: hidden; }
  body {
    background: var(--page-bg);
    position: relative;
    font-family: "Open Sans", sans-serif;
  }
  .card {
    position: absolute;
    left: 150px;
    width: 900px;
    height: 514px;
    background: var(--card-bg);
    box-shadow: 0 6px 20px rgba(0,0,0,0.12);
    overflow: hidden;
  }
  .card-back { top: 30px; }
  .card-front { top: 576px; }

  /* Back side */
  .back-circle {
    position: absolute;
    left: 260px; top: 67px;
    width: 380px; height: 380px;
    border-radius: 50%;
    background: var(--faint-circle);
  }
  .back-name {
    position: absolute;
    left: 0; right: 0; top: 150px;
    text-align: center;
    font-family: "Cinzel", serif;
    font-weight: 600;
    font-size: 84px;
    line-height: 1.2;
    color: var(--brand-blue);
  }

  /* Front side */
  .front-brand {
    position: absolute;
    left: 40px; top: 110px;
    width: 360px;
    text-align: center;
  }
  .brand-dot {
    width: 104px; height: 104px;
    border-radius: 50%;
    background: var(--brand-blue);
    margin: 0 auto 18px;
  }
  .brand-name {
    font-family: "Cinzel", serif;
    font-weight: 600;
    font-size: 40px;
    line-height: 1.15;
    color: var(--brand-blue);
  }
  .front-divider {
    position: absolute;
    left: 430px; top: 80px;
    width: 1px; height: 200px;
    background: var(--divider);
  }
  .contact {
    position: absolute;
    left: 462px; top: 78px;
  }
  .person-name {
    font-family: "Cinzel", serif;
    font-weight: 600;
    font-size: 31px;
    color: var(--brand-blue);
  }
  .person-title {
    font-family: "Cinzel", serif;
    font-size: 25px;
    color: var(--text-muted);
    margin-bottom: 16px;
  }
  .contact-line {
    display: flex;
    align-items: center;
    gap: 10px;
    font-size: 20px;
    color: var(--text-body);
    line-height: 1.6;
  }
  .contact-line svg { width: 18px; height: 18px; flex: none; }
  .wave { position: absolute; left: 0; top: 0; width: 900px; height: 514px; }
  .tagline {
    position: absolute;
    left: 0; right: 0; bottom: 22px;
    text-align: center;
    font-family: "Cinzel", serif;
    font-size: 25px;
    color: var(--text-dark);
  }
</style>
</head>
<body>
  <section class="card card-back" aria-label="Card back">
    <div class="back-circle"></div>
    <div class="back-name">Harborline<br>Renewal</div>
  </section>

  <section class="card card-front" aria-label="Card front">
    <svg class="wave" viewBox="0 0 900 514" aria-hidden="true">
      <path d="M0 392 C260 470 560 330 900 300 L900 514 L0 514 Z" fill="var(--wave-light)"/>
      <path d="M0 392 C260 470 560 330 900 300 L900 310 C560 345 260 485 0 412 Z" fill="var(--wave-dark)"/>
      <path d="M0 425 C260 492 560 352 900 322" fill="none" stroke="#ffffff" stroke-width="3"/>
    </svg>

    <div class="front-brand">
      <div class="brand-dot"></div>
      <div class="brand-name">Harborline<br>Renewal</div>
    </div>

    <div class="front-divider"></div>

    <div class="contact">
      <div class="person-name">Darnell Quisby</div>
      <div class="person-title">Title</div>
      <div class="contact-line">
        <svg viewBox="0 0 20 20"><circle cx="10" cy="10" r="10" fill="var(--brand-blue)"/><path d="M7 5 L9 8 L8 9 Q9 11.5 11 12 L12 11 L15 13 L14 15 Q8 15 5 7 Z" fill="#fff"/></svg>
        <span>555-318-2046</span>
      </div>
      <div class="contact-line">
        <svg viewBox="0 0 20 20"><circle cx="10" cy="10" r="10" fill="var(--brand-blue)"/><rect x="5" y="6.5" width="10" height="7" fill="#fff"/><path d="M5 6.5 L10 10.5 L15 6.5" fill="none" stroke="var(--brand-blue)" stroke-width="1.2"/></svg>
        <span>Darnell@HarborlineRenewal.example</span>
      </div>
      <div class="contact-line">
        <svg viewBox="0 0 20 20"><circle cx="10" cy="10" r="10" fill="var(--brand-blue)"/><circle cx="10" cy="10" r="5.5" fill="none" stroke="#fff" stroke-width="1.2"/><path d="M4.5 10 H15.5 M10 4.5 V15.5" stroke="#fff" stroke-width="1.2"/></svg>
        <span>www.HarborlineRenewal.example</span>
      </div>
    </div>

    <div class="tagline">Specializing in Water Damage Restoration</div>
  </section>
</body>
</html>
```